Laser Tattoo Removal Business Cards

We are looking for a professional business card design for a laser tattoo removal business. Ideally looking for a black business card design. The name of the business is Brightline Tattoo Removal. We place our cards at local tattoo shops so we ideally are looking for something trendy/edgy to draw both male and female clientele in.

Target Market(s)

Male/Female ages 18-60

Contact Information for Business Card

black background ideally.. hoping to stay within greys, whites and black

Font styles to use
Serif
Sans Serif

Colors
121212
a9a9a9
5c5c5c
f5f5f5
ffffff
7f7f7f
606060
848484
9d9d9d

Requirements
Must have
• Employee Info:
• Melissa Thornbury
• Chief Executive Offer
• m: 919.537.2846
• w: 919.362.4178
• f: 919.685.3907
• mthornbury@brightlinetattooremoval.example
• Address:
• 4615 Oakmere Pkwy, Suite 210
• Raleigh, NC 27654
• Website:
• www.brightlinetattooremoval.example
Nice to have
• Myabe business name on back or logo on back and employee info on the front

```html
<!DOCTYPE html>
<html lang="en">
<head>
<meta charset="utf-8">
<title>Brightline Tattoo Removal – Business Card</title>
<link rel="stylesheet" href="https://fonts.googleapis.com/css2?family=Roboto:wght@400;500;700&display=swap">
<style>
  :root {
    --ink: #121212;
    --paper: #dcdcdc;
    --paper-light: #e6e6e6;
    --stripe: #7f7f7f;
    --mid-grey: #5c5c5c;
    --soft-grey: #a9a9a9;
    --white: #ffffff;
    --off-white: #f5f5f5;
    --backdrop: #a3a3a3;
  }
  * { box-sizing: border-box; margin: 0; padding: 0; }
  html, body {
    width: 1105px;
    height: 1200px;
    overflow: hidden;
  }
  body {
    background: var(--backdrop);
    font-family: "Roboto", Arial, sans-serif;
    position: relative;
  }
  .card {
    position: absolute;
    left: 112px;
    width: 880px;
    height: 502px;
    overflow: hidden;
  }
  .card--front { top: 100px; background: linear-gradient(135deg, var(--paper-light), var(--paper)); }
  .card--back { top: 620px; background: var(--ink); }

  .front-shape { position: absolute; inset: 0; width: 880px; height: 502px; }

  .contact {
    position: absolute;
    left: 52px;
    top: 158px;
    color: var(--off-white);
    font-size: 20px;
    line-height: 28px;
  }
  .contact__address { margin-bottom: 12px; }
  .contact__list { list-style: none; }
  .contact__list li { display: flex; align-items: center; gap: 12px; }
  .contact__icon { width: 16px; height: 16px; fill: var(--off-white); flex: none; }

  .person { margin-top: 22px; }
  .person__name {
    font-size: 26px;
    font-weight: 500;
    letter-spacing: 0.5px;
    line-height: 30px;
    text-transform: uppercase;
    color: var(--white);
  }
  .person__title { font-size: 20px; line-height: 26px; }
  .person__rule {
    width: 34px;
    height: 1px;
    background: var(--off-white);
    margin: 10px 0 8px;
  }
  .person__email { font-size: 19px; }

  .brand-name {
    position: absolute;
    font-weight: 500;
    text-transform: uppercase;
    text-align: center;
    letter-spacing: 4px;
    line-height: 1.35;
  }
  .card--front .brand-name {
    left: 480px;
    width: 380px;
    top: 90px;
    font-size: 30px;
    color: var(--ink);
  }
  .card--back .brand-name {
    left: 0;
    width: 880px;
    top: 170px;
    font-size: 44px;
    color: var(--soft-grey);
  }
  .back-site {
    position: absolute;
    left: 0;
    width: 880px;
    top: 420px;
    text-align: center;
    font-size: 20px;
    letter-spacing: 3.5px;
    color: var(--off-white);
  }
</style>
</head>
<body>

<section class="card card--front" aria-label="Business card front">
  <svg class="front-shape" viewBox="0 0 880 502" aria-hidden="true">
    <path d="M0,0 L250,0 C430,60 500,270 462,502 L0,502 Z" fill="var(--stripe)"/>
    <path d="M0,0 L214,0 C392,50 470,260 440,502 L0,502 Z" fill="var(--ink)"/>
  </svg>

  <div class="contact">
    <p class="contact__address">4615 Oakmere Pkwy, Suite 210<br>Raleigh, NC 27654</p>
    <ul class="contact__list">
      <li>
        <svg class="contact__icon" viewBox="0 0 24 24" aria-hidden="true"><path d="M6.6 10.8a15.1 15.1 0 0 0 6.6 6.6l2.2-2.2a1 1 0 0 1 1-.25 11.4 11.4 0 0 0 3.6.57 1 1 0 0 1 1 1V20a1 1 0 0 1-1 1A17 17 0 0 1 3 4a1 1 0 0 1 1-1h3.5a1 1 0 0 1 1 1c0 1.25.2 2.45.57 3.6a1 1 0 0 1-.25 1z"/></svg>
        <span>919.362.4178</span>
      </li>
      <li>
        <svg class="contact__icon" viewBox="0 0 24 24" aria-hidden="true"><path d="M7 1h10a2 2 0 0 1 2 2v18a2 2 0 0 1-2 2H7a2 2 0 0 1-2-2V3a2 2 0 0 1 2-2zm0 3v15h10V4zm5 16.2a1 1 0 1 0 0 .1z"/></svg>
        <span>919.537.2846</span>
      </li>
      <li>
        <svg class="contact__icon" viewBox="0 0 24 24" aria-hidden="true"><path d="M6 2h12v6H6zM3 9h18a2 2 0 0 1 2 2v7h-4v4H5v-4H1v-7a2 2 0 0 1 2-2zm4 7v4h10v-4z"/></svg>
        <span>919.685.3907</span>
      </li>
      <li>
        <svg class="contact__icon" viewBox="0 0 24 24" aria-hidden="true"><path d="M12 2a10 10 0 1 0 0 20 10 10 0 0 0 0-20zm-1 17.9A8 8 0 0 1 4.1 11H8l3 3zm6.9-2.4A2 2 0 0 0 16 16h-1v-3l-5-5h2V6h2.5A8 8 0 0 1 17.9 17.5z"/></svg>
        <span>www.brightlinetattooremoval.example</span>
      </li>
    </ul>

    <div class="person">
      <p class="person__name">Melissa Thornbury</p>
      <p class="person__title">Chief Executive Offer</p>
      <div class="person__rule"></div>
      <p class="person__email">mthornbury@brightlinetattooremoval.example</p>
    </div>
  </div>

  <p class="brand-name">Brightline<br>Tattoo Removal</p>
</section>

<section class="card card--back" aria-label="Business card back">
  <p class="brand-name">Brightline<br>Tattoo Removal</p>
  <p class="back-site">www.brightlinetattooremoval.example</p>
</section>

</body>
</html>
```